Video Streaming Website Design Needed

We are a non-profit organization and currently have a website called LumenHourly.com
We want to launch a new version of the site that will look completely different. It is a video streaming site. We have the programmers who will work on it but we just need a designer.
We have an idea of what we want the layout to be. You can check out samples of the idea we have for the rough layout.
http://lumenhourly.com/images/LH_2.0_Homepage2.jpg
http://lumenhourly.com/images/LH_2.0_Video_Page.jpg
http://lumenhourly.com/images/LH_2.0_Individual_Speakers_Page.jpg
http://lumenhourly.com/images/LH_2.0_Registration_Page.jpg
Those are just some of our pages we plan on having.
This is a Jewish site and we have holidays through out the year and we would like to incorporate sort of a theme for each holiday using a background design change. For example, this site http://images.pvd7.layoutbarn-demo.com/qx_48217/index.html , has a nice background and maybe we can use a similar idea to change the theme of the background depending on the holiday.
Target Market(s)
Jews and spiritual minded people. Men & Women. Ages 16-55.
Industry/Entity Type
Non-Profit
Look and feel
Each slider illustrates characteristics of the customer's brand and the style your logo design should communicate.

```html
<!DOCTYPE html>
<html lang="en">
<head>
<meta charset="utf-8">
<title>LumenHourly – Sign Up</title>
<link rel="stylesheet" href="https://fonts.googleapis.com/css2?family=Roboto:wght@400;500;700&display=swap">
<style>
  :root{
    --bg-top:#2a6bc9;
    --bg-bottom:#6aa3e2;
    --panel:#eef1f5;
    --nav:#2a70d2;
    --nav-dark:#1c56ad;
    --link:#1e5fc2;
    --text:#2b2f36;
    --muted:#8a9099;
    --row-alt:#dfe9f7;
    --card:#e4e9f0;
    --dim:rgba(18,62,150,.34);
    --modal:#f4f4f4;
    --field-border:#c9ccd1;
    --cta:#1c7de6;
    --cta-dark:#0e5fc4;
  }
  *{box-sizing:border-box;margin:0;padding:0}
  html,body{width:1200px;height:952px;overflow:hidden}
  body{position:relative;font-family:"Roboto",Arial,sans-serif;color:var(--text);
    background:linear-gradient(160deg,var(--bg-top),var(--bg-bottom) 70%,#4d8ad6)}
  .abs{position:absolute}
  .backdrop-photo{left:0;top:0;width:1200px;height:952px;
    background:radial-gradient(ellipse 260px 420px at 1080px 480px,rgba(220,235,250,.45),transparent 70%),
               radial-gradient(ellipse 300px 360px at 90px 700px,rgba(200,225,250,.35),transparent 70%)}
  .page{left:204px;top:59px;width:795px;height:827px;background:var(--panel);border-radius:6px}
  .brand{left:218px;top:80px;display:flex;align-items:center;gap:8px;font-size:38px;font-weight:500;color:#1b4aa8;letter-spacing:-.5px}
  .brand .dot{width:44px;height:44px;border-radius:50%;background:#1b4aa8}
  .date{right:327px;top:66px;font-size:10px;font-weight:500;color:#555;text-align:right;line-height:16px}
  .date a{color:var(--link);text-decoration:none}
  .date span{color:#888}
  .donate{left:885px;top:59px;width:103px;height:37px;background:var(--nav);border-radius:0 0 4px 4px;
    color:#fff;font-size:15px;font-weight:500;display:flex;align-items:center;justify-content:center}
  .donate b{font-weight:400;color:#8cc6ff}
  .nav{left:213px;top:151px;width:777px;height:41px;background:linear-gradient(#3480de,var(--nav-dark));border-radius:4px}
  .nav ul{list-style:none;display:flex;gap:21px;position:absolute;left:20px;top:14px;font-size:11px;font-weight:500;color:#e8f0ff}
  .search{left:521px;top:8px;width:249px;height:25px;background:#f2f4f7;border-radius:3px;display:flex;align-items:center}
  .search svg{margin:0 6px}
  .search .ph{flex:1;font-size:10px;color:#555;border-left:1px solid #ccc;padding-left:7px;line-height:25px}
  .search .btn{width:57px;height:23px;margin-right:1px;background:var(--nav-dark);border-radius:2px;color:#fff;font-size:11px;text-align:center;line-height:23px}
  .ad{left:213px;width:97px;border:1px solid #222}
  .video{left:318px;top:199px;width:408px;height:306px;background:linear-gradient(135deg,#3b4150,#1d2432 55%,#2c4f8c)}
  .controls{left:318px;top:480px;width:408px;height:25px;background:#cfd3d8}
  .sponsor{left:319px;top:513px;width:407px;height:62px;background:var(--nav);border-radius:0 0 4px 4px;color:#fff;text-align:center}
  .sponsor p{font-size:12px;font-weight:500;line-height:17px}
  .related{left:734px;top:199px;width:256px;height:378px;background:var(--card);border-radius:4px 4px 0 0}
  .related h2{font-size:15px;font-weight:500;color:#555;padding:9px 11px}
  .row{left:0;width:243px}
  .row.alt{background:var(--row-alt)}
  .row .t{position:absolute;left:69px;font-size:9px;font-weight:500;color:#333}
  .thumb{left:10px;top:7px;width:49px;height:41px;background:linear-gradient(#8a8f98,#3e434c)}
  .meta{left:69px;top:11px;font-size:9px;line-height:14px;color:#555}
  .meta b{color:#333;font-weight:500}
  .scroll{left:244px;top:44px;width:11px;height:334px;background:#e9ecf0;border-left:1px solid #ccd}
  .comments-head{left:330px;top:585px;width:386px;font-size:12px;font-weight:500;color:var(--link);display:flex;justify-content:space-between}
  .respond{left:319px;top:606px;width:407px;height:28px;background:var(--card);border-radius:3px;font-size:12px;color:#666;padding:7px 12px}
  .comment{left:319px;width:407px;height:44px;background:var(--card);border-radius:3px;padding:8px 12px;font-size:10.5px;line-height:17px}
  .comment a{color:var(--link);text-decoration:none}
  .comment span{color:var(--muted)}
  .right-ad{left:735px;top:606px;width:255px;height:183px;border:1px solid #333;background:linear-gradient(90deg,#d8cfc6,#f2ede8 50%,#ffffff)}
  .footer{left:204px;top:810px;width:795px;text-align:center;font-size:9px;color:#777;line-height:14px}
  .footer strong{display:block;color:#1b3f8a;font-size:10px;margin-bottom:2px}
  .dim{left:0;top:0;width:1200px;height:952px;background:var(--dim)}
  .modal{left:334px;top:241px;width:552px;height:285px;background:var(--modal)}
  .modal h1{position:absolute;left:31px;top:40px;font-size:18px;font-weight:500;color:#111}
  .close{left:521px;top:15px;font-size:14px;color:#bbb}
  .field{width:209px;height:27px;background:#fff;border:1px solid var(--field-border);border-radius:2px;font-size:10.5px;color:#888;padding-left:10px;line-height:25px}
  .field.select{color:#333}
  .field.select i{position:absolute;right:0;top:0;width:24px;height:25px;border-left:1px solid var(--field-border);background:#eee}
  .check{display:flex;align-items:center;gap:11px;font-size:9.5px;color:#222;white-space:nowrap}
  .check i{width:14px;height:14px;border:1px solid #b8bbc0;border-radius:3px;background:#fff;flex:none}
  .cta{left:349px;top:223px;width:146px;height:27px;background:linear-gradient(var(--cta),var(--cta-dark));border-radius:2px;color:#fff;font-size:13px;font-weight:700;text-align:center;line-height:27px}
</style>
</head>
<body>
  <div class="abs backdrop-photo" role="img" aria-label="Photograph of a man praying in a prayer shawl"></div>

  <div class="abs page"></div>
  <div class="abs brand"><span class="dot"></span>LumenHourly</div>
  <div class="abs date">Wednesday May 18 2011 - Lyar 14, 5771<br><a>Join Now</a> <span>|</span> Login</div>
  <div class="abs donate">Donate<b>Now</b></div>

  <nav class="abs nav">
    <ul><li>About Torah</li><li>Videos</li><li>Speakers</li><li>Jewish Links</li><li>Contact Us</li><li>Privacy &amp; Terms</li></ul>
    <div class="abs search">
      <svg width="16" height="16" viewBox="0 0 16 16"><circle cx="6.5" cy="6.5" r="5" fill="none" stroke="#888" stroke-width="1.5"/><line x1="10" y1="10" x2="15" y2="15" stroke="#888" stroke-width="1.6"/></svg>
      <span class="ph">Search</span><span class="btn">Search</span>
    </div>
  </nav>

  <div class="abs ad" style="top:199px;height:97px;background:linear-gradient(#6b4a20,#c8902c)" role="img" aria-label="Community campaign banner"></div>
  <div class="abs ad" style="top:305px;height:99px;background:linear-gradient(135deg,#111,#3a1d1d 60%,#1a2a4a)" role="img" aria-label="Lecture series banner"></div>
  <div class="abs ad" style="top:411px;height:68px;background:linear-gradient(#d7dde8,#8fa3c4)" role="img" aria-label="Speaker website banner"></div>
  <div class="abs ad" style="top:486px;height:101px;background:linear-gradient(#f4e9c9,#e2b86a)" role="img" aria-label="Child protection campaign illustration"></div>
  <div class="abs ad" style="top:596px;height:98px;background:linear-gradient(#1c1a18,#6a6660 55%,#e7e7e7)" role="img" aria-label="Shabbat hospitality banner with candles"></div>
  <div class="abs ad" style="top:703px;height:86px;background:linear-gradient(#2a2a2a,#050505)" role="img" aria-label="Jewellery advertisement"></div>

  <div class="abs video" role="img" aria-label="Lecture video frame with speaker"></div>
  <div class="abs controls"><svg class="abs" style="left:8px;top:7px" width="10" height="12"><path d="M0 0L10 6L0 12Z" fill="#555"/></svg></div>
  <div class="abs sponsor">
    <p style="margin-top:3px">This Lecture is Sponsored for the:</p>
    <p style="font-size:13px">Refuah Shelema/Speedy Recovery for Dalia Bat Miriam</p>
    <p style="font-size:11px;color:#d6e6ff">Click Here to Sponsor a Lecture</p>
  </div>

  <section class="abs related">
    <h2>Related Lectures</h2>
    <div class="abs row alt" style="top:45px;height:48px"><span class="t" style="top:9px">Weekly Parsha Insight</span></div>
    <div class="abs row" style="top:100px;height:49px"><span class="t" style="top:28px">Growth After Winter</span></div>
    <div class="abs row alt" style="top:154px;height:49px"><span class="t" style="top:9px">Bitachon and the Teacher</span></div>
    <div class="abs row" style="top:210px;height:48px"><span class="t" style="top:9px">Shabbat Preparation</span></div>
    <div class="abs row alt" style="top:264px;height:48px"><span class="t" style="top:9px">The Hidden Secret</span></div>
    <div class="abs row" style="top:319px;height:52px">
      <div class="abs thumb" role="img" aria-label="Speaker portrait"></div>
      <div class="abs meta"><b>R. Eliezer Brandt</b><br>R. Zechariah<br>views:120</div>
    </div>
    <div class="abs scroll"></div>
  </section>

  <div class="abs comments-head"><span>All Comments (3)</span><span>See All</span></div>
  <div class="abs respond">Respond to this Video</div>
  <div class="abs comment" style="top:643px">omg. this is too much. i'm dying<br><a>shofarsound22</a> <span>1 day ago</span></div>
  <div class="abs comment" style="top:694px">Such a beautiful video! True Jewish message of peace.<br><a>shofarsound22</a> <span>1 day ago</span></div>
  <div class="abs comment" style="top:743px">omg. this is too much. i'm dying<br><a>shofarsound22</a> <span>1 day ago</span></div>

  <div class="abs right-ad" role="img" aria-label="Charity appeal advertisement with photograph of a child"></div>

  <footer class="abs footer">
    <strong>© Copyright LumenHourly.com 2007 - 2011. All Rights Reserved.</strong>
    The content on LumenHourly.com and related sites is for personal use only. It may not be distributed,<br>
    duplicated, broadcasted or otherwise reproduced in any way, shape or form without express written<br>
    permission from us. For permission to show content publicly, please contact us at hello@lumenhourly.org
  </footer>

  <div class="abs dim"></div>

  <div class="abs modal" role="dialog" aria-label="Sign Up">
    <h1>Sign Up</h1>
    <div class="abs close">✕</div>
    <div class="abs field" style="left:29px;top:85px">Email</div>
    <div class="abs field" style="left:29px;top:123px">Password</div>
    <div class="abs field" style="left:29px;top:160px">Confirm password</div>
    <div class="abs field" style="left:288px;top:85px">First Name</div>
    <div class="abs field" style="left:288px;top:123px">Last Name</div>
    <div class="abs field select" style="left:288px;top:160px">United Kingdom<i><svg class="abs" style="left:8px;top:10px" width="8" height="5"><path d="M0 0H8L4 5Z" fill="#333"/></svg></i></div>
    <div class="abs check" style="left:29px;top:205px"><i></i>I have read and agree to the terms and services</div>
    <div class="abs check" style="left:29px;top:231px"><i></i>Yes i would like to receive email notifications</div>
    <div class="abs cta">SIGN UP NOW</div>
  </div>
</body>
</html>
```